Harbor Loom Floors Letterhead

Letterhead used for business reasons. It must be editable and easy to use.

Address is 2715 W. Pelican Lane Englewood FL 34187 - 941.382.6519

```html
<!DOCTYPE html>
<html lang="en">
<head>
<meta charset="utf-8">
<title>Harbor Loom Floors Letterhead</title>
<link rel="stylesheet" href="https://fonts.googleapis.com/css2?family=Lato:wght@400;700&family=Montserrat:wght@400&family=Italianno&display=swap">
<style>
  :root {
    --backdrop: #e6e6e6;
    --paper: #ffffff;
    --brand-orange: #e08a26;
    --brand-taupe: #958a85;
    --ink: #1c1c1c;
  }
  * { margin: 0; padding: 0; box-sizing: border-box; }
  html, body {
    width: 1200px; height: 1079px; overflow: hidden;
    background: var(--backdrop);
  }
  .letterhead {
    position: absolute; left: 246px; top: 40px;
    width: 707px; height: 1000px;
    background: var(--paper);
    box-shadow: 0 2px 10px rgba(0,0,0,0.12);
    font-family: "Lato", sans-serif; color: var(--ink);
  }
  .brand-name {
    position: absolute; left: 36px; top: 62px;
    font-family: "Lato", sans-serif; font-weight: 400;
    font-size: 44px; letter-spacing: 0.5px;
    color: var(--brand-orange); line-height: 1;
  }
  .contact {
    position: absolute; left: 514px; top: 73px;
    height: 50px; border-left: 1.5px solid var(--brand-orange);
    padding-left: 21px;
    font-family: "Montserrat", sans-serif; font-size: 12.5px; line-height: 17px;
  }
  .contact .phone { margin-top: 8px; display: flex; align-items: center; gap: 4px; }
  .contact svg { width: 10px; height: 10px; }
  .block { position: absolute; left: 36px; font-size: 14px; line-height: 17px; }
  .date { top: 258px; }
  .recipient { top: 293px; }
  .company { top: 362px; }
  .salutation { top: 445px; font-size: 17.5px; font-weight: 700; }
  .body-copy { top: 507px; width: 637px; font-size: 13px; line-height: 15.6px; text-align: justify; }
  .body-copy p + p { margin-top: 15px; }
  .closing { top: 791px; }
  .signature {
    position: absolute; left: 36px; top: 858px;
    font-family: "Italianno", cursive; font-size: 40px; line-height: 1;
  }
  .footer-band {
    position: absolute; left: 0; right: 0; top: 967px; height: 23px;
    display: flex;
  }
  .footer-band .accent { width: 527px; background: var(--brand-orange); }
  .footer-band .neutral { flex: 1; background: var(--brand-taupe); }
</style>
</head>
<body>
  <main class="letterhead">
    <header>
      <div class="brand-name">Harbor Loom Floors</div>
      <address class="contact" style="font-style: normal;">
        <div>2715 W. Pelican Lane</div>
        <div>Englewood FL 34187</div>
        <div class="phone">
          <svg viewBox="0 0 24 24" aria-hidden="true"><path fill="#e08a26" d="M6.6 10.8a15 15 0 0 0 6.6 6.6l2.2-2.2a1 1 0 0 1 1-.25 11.4 11.4 0 0 0 3.6.57 1 1 0 0 1 1 1V20a1 1 0 0 1-1 1A17 17 0 0 1 3 4a1 1 0 0 1 1-1h3.5a1 1 0 0 1 1 1c0 1.25.2 2.45.57 3.57a1 1 0 0 1-.25 1z"/></svg>
          <span>941.382.6519</span>
        </div>
      </address>
    </header>

    <div class="block date">January-03-2020</div>
    <div class="block recipient">Mr, Aaron Whitfield<br>President</div>
    <div class="block company">Brightway Holdings<br>123 Street Name, Suite# 10<br>City, State, 120023</div>
    <div class="block salutation">Dear Mr, Aaron</div>

    <section class="block body-copy">
      <p>Lorem ipsum dolor sit amet, consectetur adipiscing elit, sed do eiusmod tempor incididunt ut labore et dolore magna aliqua. Ut enim ad minim veniam, quis nostrud exercitation ullamco laboris nisi ut aliquip ex ea commodo consequat. Duis aute irure dolor in reprehenderit in voluptate velit esse cillum dolore eu fugiat nulla pariatur.</p>
      <p>Lorem ipsum dolor sit amet, consectetur adipiscing elit, sed do eiusmod tempor incididunt ut labore et dolore magna aliqua. Ut enim ad minim veniam, quis nostrud exercitation ullamco laboris nisi ut aliquip ex ea commodo consequat. Duis aute irure dolor in reprehenderit in voluptate velit esse cillum dolore eu fugiat nulla pariatur.</p>
      <p>Lorem ipsum dolor sit amet, consectetur adipiscing elit, sed do eiusmod tempor incididunt ut labore et dolore magna aliqua. Ut enim ad minim veniam, quis nostrud exercitation ullamco laboris nisi ut aliquip ex ea commodo consequat.</p>
      <p>Excepteur sint occaecat cupidatat non proident, sunt in culpa qui officia deserunt mollit anim id est laborum. re et dolore magnam aliquam quaerat voluptatem.</p>
    </section>

    <div class="block closing">Regards</div>
    <div class="signature">Clara Bennett</div>

    <footer class="footer-band">
      <div class="accent"></div>
      <div class="neutral"></div>
    </footer>
  </main>
</body>
</html>
```